Love cats? Love the planet? We need a design for the most eco-friendly cat grass kit box ever!

We need a box designed for our new product - the world's most eco-friendly cat grass kit ever!

Text and documents attached. Text can be copied and pasted. It has been spell-checked already.

Some pictures need to be sourced and/or drawn.

It needs to be eye-catching in its simplicity and minimalism. Not too many colors, swirls, curlicues and stuff. Just simple. And the 'green' nature of it (biodegradability, 'save the planet', recycle, re-use, sustainable contents etc needs to be visible from a distance to stand out from the crowd).

Final design needs to communicate love of cats and the planet.

Target Market(s)

Apartment-dwelling cat owners

Industry/Entity Type

Pet Care

Other font styles liked:
• Comfortaa

Colors

Designer to choose colors to be used in the design.

Requirements
Must have
• Clear, clean, simple and eye-catching design. Not overloaded with images and text. A cute cartoon/drawn cat munching on the cat grass.
• A drawn pot that heavily matches the actual pot in terms of color, shape and texture.

```html
<!DOCTYPE html>
<html lang="en">
<head>
<meta charset="utf-8">
<title>Cat Grass Kit – Box Panels</title>
<link href="https://fonts.googleapis.com/css2?family=Fredoka:wght@600&family=Kanit:wght@400;500;600&display=swap" rel="stylesheet">
<style>
  :root {
    --stage: #c9ccd6;
    --leaf: #8dc43f;
    --leaf-deep: #4e9a3a;
    --meadow: #5aa83e;
    --soil: #3a1d14;
    --sun: #f4b324;
    --sun-deep: #e98b1e;
    --paw: #e8e03a;
    --cream: #ffffff;
    --ink: #3a2a22;
    --teal: #1f8f7d;
    --fur: #d98a3c;
  }
  * { box-sizing: border-box; margin: 0; padding: 0; }
  html, body { width: 1200px; height: 1200px; overflow: hidden; }
  body {
    background: var(--stage);
    font-family: "Kanit", sans-serif;
    position: relative;
  }
  .panel { position: absolute; overflow: hidden; width: 520px; height: 520px; }

  .display {
    font-family: "Fredoka", "Kanit", sans-serif; font-weight: 600;
    color: var(--sun); text-align: center; line-height: 0.95;
    position: relative; z-index: 2;
  }
  .paws {
    position: absolute; border-radius: 50%;
    background: var(--paw); opacity: 0.55; z-index: 1;
  }

  /* lid panel */
  .lid { left: 60px; top: 80px; background: var(--leaf); }
  .lid__title {
    position: absolute; left: 130px; top: 150px; width: 260px;
    font-size: 66px;
  }
  .lid__paws { left: 330px; top: 120px; width: 90px; height: 90px; }

  /* front panel */
  .front { left: 60px; top: 620px; background: var(--leaf); }
  .front__title {
    position: absolute; left: 60px; top: 40px; width: 210px;
    font-size: 56px;
  }
  .front__paws { left: 235px; top: 28px; width: 80px; height: 80px; }
  .brand {
    position: absolute; display: flex; align-items: center; gap: 8px;
  }
  .brand__mark { background: var(--ink); }
  .brand__name {
    font-family: "Kanit", sans-serif; font-weight: 600;
    color: var(--ink); line-height: 1;
  }
  .front .brand { right: 40px; top: 130px; }
  .front .brand__mark { width: 18px; height: 18px; }
  .front .brand__name { font-size: 24px; }
  .front__meadow {
    position: absolute; left: 0; top: 290px; width: 520px; height: 190px;
    background: linear-gradient(180deg, var(--meadow) 0%, var(--leaf-deep) 100%);
  }
  .badge {
    position: absolute; left: 70px; top: 315px; width: 80px; height: 80px;
    border-radius: 50%; background: var(--teal); border: 4px solid #d8efe8;
  }
  .front__claim {
    position: absolute; left: 56px; top: 405px;
    font-size: 17px; line-height: 1.2; color: var(--cream); font-weight: 500;
  }
  .front__cats {
    position: absolute; left: 250px; top: 245px; width: 250px; height: 225px;
    border-radius: 100px 100px 0 0;
    background: linear-gradient(160deg, var(--fur) 0%, #f2f0e6 60%, #d8d8d2 100%);
  }
  .front__band {
    position: absolute; left: 0; bottom: 0; width: 520px; height: 50px;
    background: var(--soil); color: var(--cream);
    display: flex; align-items: center; justify-content: center;
    font-size: 16px; font-weight: 500; letter-spacing: 1px;
  }

  /* side panel */
  .side { left: 600px; top: 620px; background: var(--cream); }
  .side .brand { right: 24px; top: 20px; }
  .side .brand__mark { width: 11px; height: 11px; }
  .side .brand__name { font-size: 14px; }
  .side__title {
    position: absolute; left: 28px; top: 52px; font-size: 30px;
    color: var(--sun-deep); text-align: left;
  }
  .side__recycle {
    position: absolute; right: 34px; top: 104px; width: 36px; height: 36px;
  }
  .side__copy {
    position: absolute; left: 28px; top: 104px; width: 330px;
    font-size: 13px; line-height: 1.45; color: var(--leaf-deep);
  }
  .side__warning {
    position: absolute; left: 28px; top: 250px; width: 330px;
    font-size: 12px; line-height: 1.45; color: var(--leaf-deep);
  }
  .side__warning-label {
    display: inline-block; background: var(--leaf-deep); color: var(--cream);
    padding: 1px 8px; margin-bottom: 6px; font-weight: 600; letter-spacing: 1px;
  }
  .side__pot {
    position: absolute; right: 34px; top: 180px; width: 80px; height: 150px;
    border-radius: 8px;
    background: linear-gradient(180deg, #7fb84a 0%, #4f8f33 55%, #5a3a26 56%, #3b2418 100%);
  }
  .side__grass {
    position: absolute; left: 0; bottom: 0; width: 520px; height: 150px;
    background: linear-gradient(180deg, rgba(141,196,63,0) 0%, rgba(141,196,63,0.55) 100%);
  }
  .side__web {
    position: absolute; left: 28px; bottom: 16px;
    font-size: 12px; color: var(--leaf-deep);
  }
</style>
</head>
<body>

<section class="panel lid">
  <div class="paws lid__paws" role="img" aria-label="Yellow paw print decoration"></div>
  <h2 class="display lid__title">CAT GRASS KIT</h2>
</section>

<section class="panel front">
  <div class="paws front__paws" role="img" aria-label="Yellow paw print decoration"></div>
  <h1 class="display front__title">CAT GRASS KIT</h1>
  <div class="brand">
    <span class="brand__mark"></span>
    <span class="brand__name">Purrch Home</span>
  </div>
  <div class="front__meadow" role="img" aria-label="Green grass meadow illustration"></div>
  <div class="badge" role="img" aria-label="Organic certification badge"></div>
  <p class="front__claim">100% non-gmo,<br>USA-grown</p>
  <div class="front__cats" role="img" aria-label="Illustration of four happy cartoon cats peeking over the grass"></div>
  <p class="front__band">THE GREENEST CAT GRASS KIT…EVER. SERIOUSLY.</p>
</section>

<section class="panel side">
  <div class="brand">
    <span class="brand__mark"></span>
    <span class="brand__name">Purrch Home</span>
  </div>
  <h2 class="display side__title">CAT GRASS KIT</h2>
  <svg class="side__recycle" viewBox="0 0 40 40" aria-label="Recyclable">
    <circle cx="20" cy="20" r="17" fill="none" stroke="var(--leaf-deep)" stroke-width="3"/>
    <path d="M13 22 L20 12 L27 22 M20 12 V29" fill="none" stroke="var(--leaf-deep)" stroke-width="3" stroke-linecap="round"/>
  </svg>
  <p class="side__copy">100% non-gmo, organic, USA-grown: rye seeds, oat seeds, barley seeds and wheat seeds. 100% USA-made organic coconut growing mix. Seed blend may vary by season and availability.</p>
  <div class="side__warning">
    <span class="side__warning-label">WARNING</span>
    <p>Only for cats. Not for human consumption.<br>Keep out of reach of children.</p>
  </div>
  <div class="side__grass" role="img" aria-label="Soft grass blades along the bottom edge"></div>
  <div class="side__pot" role="img" aria-label="Pot of growing cat grass"></div>
  <p class="side__web">www.purrchhome.com</p>
</section>

</body>
</html>
```